KorvaLex Injury Solicitors

We need a modern, sleek letterhead that is professional.

In relation to the footer, we would like to have firm contact details there ideally, however you must also insert at the bottom of each page the following....

Liability limited by a scheme approved under the Professional Standards Legislation.

From the attachment you can extract the firm logo. Also, I would like the Accredited specialist circle on the letterhead also.

Also, I would like you to create a document that can easily be edited for change of contact details, as these are likely to change.

Industry/Entity Type

It Professional

Font styles to use
Sans Serif

Colors
0655a3
3276b5
85abd2
0492cd
33a6d7
85cae6
cee9f5
eaf1f7
cbcbcb

Requirements
Must have
• Ph: 9317-5802
• F: 9581-3274
• M 0438-615-249
• mt@korvalex.com.au
• www.korvalex.com.au
Nice to have
• the word document gives you an idea of what I like. I am happy for your to amaze me with your creativity.

```html
<!DOCTYPE html>
<html lang="en">
<head>
<meta charset="utf-8">
<title>KorvaLex Injury Solicitors – Letterhead</title>
<link rel="stylesheet" href="https://fonts.googleapis.com/css2?family=Arimo:wght@400;700&family=Source+Sans+3:wght@400&display=swap">
<style>
  :root {
    --brand-deep: #0655a3;
    --brand-mid: #3276b5;
    --brand-light: #85abd2;
    --sky: #0492cd;
    --sky-soft: #85cae6;
    --mist: #eaf1f7;
    --ink: #111111;
    --ink-soft: #3d3d3d;
    --grey-rule: #cbcbcb;
    --backdrop: #e6e9ed;
    --paper: #ffffff;
  }
  html, body {
    margin: 0;
    padding: 0;
    width: 1200px;
    height: 1200px;
    overflow: hidden;
    background: var(--backdrop);
  }
  .letterhead {
    position: absolute;
    left: 175px;
    top: 50px;
    width: 850px;
    height: 1100px;
    background: var(--paper);
    box-shadow: 0 2px 14px rgba(0,0,0,0.12);
    overflow: hidden;
  }
  .top-band {
    position: absolute;
    left: 0; top: 0;
    width: 100%;
    height: 12px;
    background: var(--brand-deep);
  }
  .brand {
    position: absolute;
    left: 92px;
    top: 118px;
    display: flex;
    align-items: center;
    gap: 14px;
  }
  .brand-dot {
    width: 44px;
    height: 44px;
    border-radius: 50%;
    background: var(--sky-soft);
    flex: none;
  }
  .brand-name {
    font-family: "Source Sans 3", "Myriad Pro", sans-serif;
    font-weight: 400;
    font-size: 30px;
    line-height: 32px;
    color: var(--brand-deep);
  }
  .office-contact {
    position: absolute;
    left: 583px;
    top: 46px;
    font-family: "Arimo", Arial, sans-serif;
    font-style: normal;
    font-size: 16px;
    line-height: 19.5px;
    color: var(--ink-soft);
    letter-spacing: 0.3px;
  }
  .office-contact .office-name {
    color: var(--ink);
  }
  .office-contact .label {
    display: inline-block;
    min-width: 34px;
  }
  .watermark {
    position: absolute;
    left: 231px;
    top: 346px;
    width: 450px;
    height: 450px;
  }
  .footer {
    position: absolute;
    left: 48px;
    top: 1010px;
    width: 664px;
  }
  .practice-areas {
    font-family: "Arimo", Arial, sans-serif;
    font-size: 16px;
    letter-spacing: 0.3px;
    color: var(--ink-soft);
    white-space: nowrap;
    margin: 0;
  }
  .footer-rule {
    width: 664px;
    height: 1px;
    background: var(--grey-rule);
    margin: 6px 0 8px 0;
  }
  .liability {
    font-family: "Arimo", Arial, sans-serif;
    font-size: 13px;
    color: var(--ink-soft);
    margin: 0 0 0 12px;
    letter-spacing: 0.2px;
    white-space: nowrap;
  }
  .accreditation-badge {
    position: absolute;
    left: 736px;
    top: 1006px;
    width: 58px;
    height: 58px;
  }
</style>
</head>
<body>
  <main class="letterhead">
    <div class="top-band"></div>

    <header class="brand">
      <span class="brand-dot"></span>
      <div class="brand-name">KorvaLex<br>Injury Solicitors</div>
    </header>

    <address class="office-contact">
      <div class="office-name">Northgate Office</div>
      <div>P.O. Box B418 Kelso Park</div>
      <div>NSW 2150</div>
      <div><span class="label">Ph:</span>9317-5802</div>
      <div><span class="label">F:</span>9581-3274</div>
      <div><span class="label">M:</span>0438-615-249</div>
      <div>mt@korvalex.com.au</div>
      <div>www.korvalex.com.au</div>
    </address>

    <svg class="watermark" viewBox="0 0 450 450" aria-hidden="true">
      <circle cx="225" cy="225" r="160" fill="var(--mist)" opacity="0.8"/>
    </svg>

    <footer class="footer">
      <p class="practice-areas">INSURANCE LAW | ESTATE &amp; PROPERTY LAW | FAMILY LAW | COMMERCIAL LAW</p>
      <div class="footer-rule"></div>
      <p class="liability">Liability limited by a scheme approved under the Professional Standards Legislation.</p>
    </footer>

    <svg class="accreditation-badge" viewBox="0 0 60 60" role="img" aria-label="Accredited specialist badge">
      <circle cx="30" cy="30" r="27" fill="none" stroke="var(--ink)" stroke-width="2"/>
      <circle cx="30" cy="30" r="17" fill="var(--sky)"/>
    </svg>
  </main>
</body>
</html>
```